Business card for boutique investment firm

Need a business card designed for our boutique investment firm called "BrightLedger Advisory Cost Partners". We help investors achieve lower fees through negotiation on their behalf. We have a logo to work with and a color palette. The card should incorporate our tag line "Small Steps, Lasting Gains" and space for relevant details. The look and feel should reflect the logo and our brand personality: Humble, Trustworthy, Friendly

Target Market(s)

High net worth investors who are looking for clarity around how they are being charged by their investment advisor

Industry/Entity Type

Boutique

Requirements
Must have
• Logo
Tag line: Small Steps, Lasting Gains
Space for relevant contact details: name, title, phone, email, URL, mailing address

Use these fonts: 'AvantGarde Bk BT' and 'AvantGarde Bk BT Demi'
Use these colors:
Orange = C-0 / M-60 / Y-100 / K-0
Grey = C-0 / M-0 / Y-0 / K-60

```html
<!DOCTYPE html>
<html lang="en">
<head>
<meta charset="utf-8">
<title>BrightLedger Business Card</title>
<link rel="stylesheet" href="https://fonts.googleapis.com/css2?family=Questrial&display=swap">
<style>
  :root {
    --orange: #d9731a;
    --grey: #8a8b8d;
    --grey-dark: #6f7072;
    --paper: #f2f2f2;
    --backdrop: #e4e2de;
    --rule: rgba(255,255,255,0.85);
  }
  * { margin: 0; padding: 0; box-sizing: border-box; }
  html, body {
    width: 1200px; height: 900px; overflow: hidden;
    background: var(--backdrop);
    font-family: 'Questrial', 'Century Gothic', sans-serif;
  }
  .sheet {
    position: relative; width: 1200px; height: 900px;
    display: flex; flex-direction: column; align-items: center; justify-content: center;
    gap: 56px;
  }
  .card {
    position: relative; width: 560px; height: 320px;
    box-shadow: 0 6px 18px rgba(0,0,0,0.14);
    overflow: hidden;
  }

  /* Front */
  .card-front { background: var(--orange); color: #fff; }
  .card-front .brand {
    position: absolute; left: 70px; top: 108px;
    display: flex; align-items: center; gap: 18px;
  }
  .brand-dot {
    width: 58px; height: 58px; border-radius: 50%;
    background: #fff; flex: none;
  }
  .brand-name { line-height: 1.05; white-space: nowrap; }
  .brand-name .primary { display: block; font-size: 40px; letter-spacing: -0.5px; }
  .brand-name .secondary { display: block; font-size: 15px; letter-spacing: 2.4px; margin-top: 2px; }
  .card-front .tagline {
    position: absolute; right: 0; top: 226px;
    display: flex; align-items: center; gap: 10px;
    font-size: 12.5px; letter-spacing: 1px; text-transform: uppercase;
  }
  .card-front .tagline::after {
    content: ""; display: block; width: 92px; height: 1px; background: var(--rule);
  }

  /* Back */
  .card-back { background: var(--paper); color: var(--grey); }
  .card-back .edge {
    position: absolute; left: 0; top: 0; bottom: 0; width: 22px; background: var(--orange);
  }
  .card-back .brand {
    position: absolute; left: 58px; top: 44px;
    display: flex; align-items: center; gap: 16px;
  }
  .card-back .brand-dot { background: var(--orange); width: 54px; height: 54px; }
  .card-back .brand-name { color: var(--grey-dark); }
  .card-back .brand-name .primary { font-size: 36px; }
  .card-back .brand-name .secondary { font-size: 13.5px; letter-spacing: 2.2px; }

  .person { position: absolute; left: 58px; top: 168px; }
  .person-name { font-size: 22px; color: var(--grey-dark); }
  .person-title { font-size: 13px; color: var(--orange); letter-spacing: 0.8px; margin-top: 4px; text-transform: uppercase; }
  .web { position: absolute; left: 58px; bottom: 38px; font-size: 15px; color: var(--grey-dark); }
  .web .accent { color: var(--orange); }

  .contact {
    position: absolute; right: 40px; top: 150px;
    font-size: 13px; line-height: 1.55; color: var(--grey-dark);
  }
  .contact .row { display: flex; gap: 10px; }
  .contact .label { color: var(--orange); width: 10px; }
  .contact address { font-style: normal; margin-top: 22px; padding-left: 20px; }
</style>
</head>
<body>
<main class="sheet">
  <section class="card card-front" aria-label="Card front">
    <div class="brand">
      <span class="brand-dot"></span>
      <span class="brand-name">
        <span class="primary">BrightLedger</span>
        <span class="secondary">Advisory Cost Partners</span>
      </span>
    </div>
    <p class="tagline">Small Steps, Lasting Gains</p>
  </section>

  <section class="card card-back" aria-label="Card back">
    <span class="edge"></span>
    <div class="brand">
      <span class="brand-dot"></span>
      <span class="brand-name">
        <span class="primary">BrightLedger</span>
        <span class="secondary">Advisory Cost Partners</span>
      </span>
    </div>
    <div class="person">
      <p class="person-name">Clara Mendes</p>
      <p class="person-title">Manager</p>
    </div>
    <p class="web">www.bright<span class="accent">ledger</span>.com</p>
    <div class="contact">
      <p class="row"><span class="label">t</span>555-204-7318</p>
      <p class="row"><span class="label">e</span>clara@brightledger.com</p>
      <address>88 Harbor Street Suite 310<br>Portland ME 04101 USA</address>
    </div>
  </section>
</main>
</body>
</html>
```